Brand new letterhead, business card, email signature etc.

We are a financial company in London, UK. Our website is www.marlowvane.com. We're wanting a complete remodel of the company colours, letter head, business cards, email signatures, etc. Looking to keep the same font for the company name. I have upload a colour palette that we want to work with. We're looking for company letterhead for outgoing letters/ correspondence, letterhead for internal documentation, email signatures, e-letters. etc. Ultimately we will redesign the entire website also. It is important that our clients get a strong, secure, warm, trustworthy, solid feeling and first impression.
Updates

Designs look the same

Target Market(s)

Institutional investors, (ultra) high net worth individuals

Industry/Entity Type

Finance, Invesments banking.

Font styles to use
Other font styles liked:
• Current font is "Champagne & Limousines"

Requirements
Must have
• Must use the colours provided on the PDF uploaded to the portal. The purple = main colour. The red = accent colour.
Nice to have
• Nice to use same font as now for the company name "Corvane". Font is "Champagne & Limousines". Nice to have some reference to the old logo flower, but only subtle.
Should not have
• Do not use the colour red from our website. Use the colours provided on the colour palette PDF that I uploaded in the portal.

```html
<!DOCTYPE html>
<html lang="en">
<head>
<meta charset="utf-8">
<title>Corvane Stationery</title>
<link rel="stylesheet" href="https://fonts.googleapis.com/css2?family=Open+Sans:wght@300;400;600;700&display=swap">
<style>
  :root{
    --backdrop:#d3d3d5;
    --paper:#ffffff;
    --paper-soft:#f3f3f3;
    --brand:#4b2463;
    --brand-deep:#2f123f;
    --brand-light:#5e3079;
    --accent:#d8321f;
    --ink:#1d1a1c;
  }
  *{margin:0;padding:0;box-sizing:border-box}
  html,body{width:1200px;height:792px;overflow:hidden}
  body{background:var(--backdrop);font-family:"Open Sans",Arial,sans-serif;color:var(--ink);position:relative}
  .piece{position:absolute;overflow:hidden;background:var(--paper)}
  .band{position:absolute;left:0;top:0;width:100%;height:100%}
  .mark-square{position:absolute;border:1.2px solid var(--brand)}
  .wordmark{position:absolute;font-family:"Open Sans",Arial,sans-serif;font-weight:300;text-transform:uppercase;letter-spacing:.2em;line-height:1;white-space:nowrap;color:var(--brand)}
  .divider{position:absolute;width:1.2px;background:var(--brand)}
  .contacts{position:absolute;list-style:none}
  .contacts li{display:flex;align-items:center;white-space:nowrap}
  .contacts svg{fill:var(--accent);flex:none}
  .person-name{position:absolute;font-weight:700;white-space:nowrap;line-height:1;color:var(--brand)}
  .person-name .accent-part{color:var(--accent)}
  .person-role{position:absolute;white-space:nowrap;line-height:1}
  .band-text{position:absolute;left:0;width:100%;text-align:center;color:#fff;white-space:nowrap}

  /* business card front */
  .card-front{left:155px;top:233px;width:194px;height:111px}
  .card-front .mark-square{left:54px;top:8px;width:22px;height:22px}
  .card-front .wordmark{left:81px;top:13px;font-size:12px}
  .card-front .person-name{left:14px;top:58px;font-size:9.5px}
  .card-front .person-role{left:39px;top:71px;font-size:5.5px;font-weight:600}
  .card-front .divider{left:98px;top:52px;height:35px}
  .card-front .contacts{left:108px;top:53px;font-size:5.3px;line-height:7.1px}
  .card-front .contacts svg{width:5px;height:5px;margin-right:3px}
  .card-front .band-text{top:97px;font-size:5.3px}

  /* business card back */
  .card-back{left:379px;top:233px;width:194px;height:111px;background:linear-gradient(100deg,var(--brand-light) 0%,var(--brand) 70%,var(--brand-deep) 100%)}
  .card-back .mark-square{left:22px;top:37px;width:38px;height:38px;border-color:#fff}
  .card-back .wordmark{left:69px;top:47px;font-size:19px;color:#fff}

  /* email signature */
  .signature{left:154px;top:401px;width:419px;height:139px}
  .signature .motif{position:absolute;left:318px;top:0;width:110px;height:118px;border-radius:50% 40% 45% 55%;background:radial-gradient(circle at 50% 45%,rgba(0,0,0,.05),rgba(0,0,0,0) 70%)}
  .signature .mark-square{left:15px;top:43px;width:48px;height:48px}
  .signature .wordmark{left:74px;top:55px;font-size:24px}
  .signature .divider{left:245px;top:21px;height:92px;width:1px}
  .signature .person-name{left:267px;top:24px;font-size:15.5px}
  .signature .person-role{left:267px;top:40px;font-size:8px;font-weight:400}
  .signature .address{position:absolute;left:267px;top:55px;font-size:8px;line-height:10px}
  .signature .contacts{left:267px;top:80px;font-size:8px;line-height:10px}
  .signature .contacts svg{width:6px;height:6px;margin-right:4px}

  /* letterhead */
  .letterhead{left:595px;top:131px;width:367px;height:519px;background:var(--paper-soft)}
  .letterhead .mark-square{left:40px;top:15px;width:40px;height:40px}
  .letterhead .wordmark{left:90px;top:26px;font-size:21px}
  .letterhead .divider{left:225px;top:9px;height:53px}
  .letterhead .contacts{left:236px;top:20px;font-size:8.8px;line-height:10px}
  .letterhead .contacts svg{width:6px;height:6px;margin-right:6px}
  .letterhead .motif{position:absolute;left:45px;top:112px;width:280px;height:300px;border-radius:48% 52% 40% 60%;background:radial-gradient(circle at 55% 45%,rgba(75,36,99,.05),rgba(0,0,0,0) 70%)}
  .letterhead .band-text{top:497px;font-size:9px;font-weight:600;display:flex;justify-content:center;align-items:center;gap:4px}
  .letterhead .band-text svg{width:7px;height:9px;fill:none;stroke:#fff;stroke-width:1.2}
</style>
</head>
<body>

<svg width="0" height="0" style="position:absolute" aria-hidden="true">
  <symbol id="icon-phone" viewBox="0 0 10 10"><path d="M2.2 1 L3.8 2.8 L3 4 Q4.3 6 6 7 L7.2 6.2 L9 7.8 L8 9 Q3 8.4 1 2 Z"/></symbol>
  <symbol id="icon-web" viewBox="0 0 10 10"><path d="M5 .5A4.5 4.5 0 1 0 5 9.5A4.5 4.5 0 1 0 5 .5ZM5 1.7A3.3 3.3 0 0 1 8.3 5H1.7A3.3 3.3 0 0 1 5 1.7Z"/></symbol>
  <symbol id="icon-mail" viewBox="0 0 10 10"><path d="M1 2.5H9V8H1ZM2 3.5V7H8V3.5L5 5.6Z"/></symbol>
</svg>

<!-- Business card, front -->
<section class="piece card-front" aria-label="Business card front">
  <svg class="band" viewBox="0 0 194 111" preserveAspectRatio="none" aria-hidden="true">
    <path d="M0 78 Q97 102 194 78 L194 111 L0 111 Z" fill="var(--brand)"/>
    <path d="M7 78 Q97 100 187 78" fill="none" stroke="var(--accent)" stroke-width="1.3"/>
  </svg>
  <span class="mark-square"></span>
  <span class="wordmark">Corvane</span>
  <p class="person-name"><span class="accent-part">Elena</span> Marsh</p>
  <p class="person-role">Managing Director</p>
  <span class="divider"></span>
  <ul class="contacts">
    <li><svg><use href="#icon-phone"/></svg>(020) 7946 0381</li>
    <li><svg><use href="#icon-phone"/></svg>(020) 7946 0382</li>
    <li><svg><use href="#icon-mail"/></svg>info@marlowvane.com</li>
    <li><svg><use href="#icon-web"/></svg>www.marlowvane.com</li>
  </ul>
  <p class="band-text">14 Ashcombe Row, Suite 3, London EC2V 7NQ</p>
</section>

<!-- Business card, back -->
<section class="piece card-back" aria-label="Business card back">
  <span class="mark-square"></span>
  <span class="wordmark">Corvane</span>
</section>

<!-- Email signature -->
<section class="piece signature" aria-label="Email signature">
  <div class="motif" role="img" aria-label="Faint flower motif behind the contact details"></div>
  <svg class="band" viewBox="0 0 419 139" preserveAspectRatio="none" aria-hidden="true">
    <path d="M0 110 Q209 138 419 110 L419 139 L0 139 Z" fill="var(--brand)"/>
    <path d="M15 110 Q209 134 404 110" fill="none" stroke="var(--accent)" stroke-width="1.4"/>
  </svg>
  <span class="mark-square"></span>
  <span class="wordmark">Corvane</span>
  <span class="divider"></span>
  <p class="person-name">Elena <span class="accent-part">Marsh</span></p>
  <p class="person-role">Co-Founder</p>
  <p class="address">14 Ashcombe Row, Suite 3<br>London EC2V 7NQ</p>
  <ul class="contacts">
    <li><svg><use href="#icon-phone"/></svg>(020) 7946 0381</li>
    <li><svg><use href="#icon-mail"/></svg>info@marlowvane.com</li>
    <li><svg><use href="#icon-web"/></svg>www.marlowvane.com</li>
  </ul>
</section>

<!-- Letterhead -->
<section class="piece letterhead" aria-label="Letterhead">
  <div class="motif" role="img" aria-label="Large faint flower motif in the page background"></div>
  <svg class="band" viewBox="0 0 367 519" preserveAspectRatio="none" aria-hidden="true">
    <path d="M0 462 Q183 520 367 462 L367 519 L0 519 Z" fill="var(--brand)"/>
    <path d="M14 462 Q183 514 353 462" fill="none" stroke="var(--accent)" stroke-width="1.8"/>
  </svg>
  <span class="mark-square"></span>
  <span class="wordmark">Corvane</span>
  <span class="divider"></span>
  <ul class="contacts">
    <li><svg><use href="#icon-phone"/></svg>(020) 7946 0381</li>
    <li><svg><use href="#icon-web"/></svg>www.marlowvane.com</li>
    <li><svg><use href="#icon-mail"/></svg>office@marlowvane.com</li>
  </ul>
  <p class="band-text"><svg viewBox="0 0 8 10"><path d="M4 9.4C1.5 6.5 1 5.2 1 4A3 3 0 0 1 7 4C7 5.2 6.5 6.5 4 9.4Z"/><circle cx="4" cy="4" r="1.1"/></svg>14 Ashcombe Row, London, EC2V 7NQ</p>
</section>

</body>
</html>
```